Bry7Legal Letterhead

Need a new letterhead for my law firm.
IDENTIFYING INFORMATION BELOW:
Anselmo R Quintara III
Attorney at Law
Address: 2847 Larkspur Blvd, Ste 300, Dallas, TX 75204
Phone: 877-482-6017
Fax: 469-738-1452
Email: bry@bry7legal.example
Website: www.bry7legal.example

Colors
0054AA
0677BA
7BADD7
CADEEF
E8F1F8

Requirements
Must have
• Logo needs to be on the letterhead, along with identifying information which is included in the project description.

```html
<!DOCTYPE html>
<html lang="en">
<head>
<meta charset="utf-8">
<title>Bry7Legal Letterhead</title>
<link rel="stylesheet" href="https://fonts.googleapis.com/css2?family=Open+Sans:wght@400;600;700&family=Lato:wght@400;700&display=swap">
<style>
  :root {
    --backdrop: #d9d9d9;
    --paper: #ffffff;
    --ink: #3a3a3a;
    --ink-dark: #1b1b1b;
    --band: #000000;
    --band-text: #ffffff;
    --accent: #0677ba;
    --accent-bright: #1a9ad9;
    --divider: #555555;
    --signature: #e8f1f8;
  }
  * { margin: 0; padding: 0; box-sizing: border-box; }
  html, body { width: 1040px; height: 1200px; overflow: hidden; background: var(--backdrop); }
  .letterhead {
    position: absolute; left: 80px; top: 33px; width: 881px; height: 1133px;
    background: var(--paper); font-family: "Open Sans", sans-serif; color: var(--ink);
    box-shadow: 0 2px 8px rgba(0,0,0,.15);
  }
  .brand {
    position: absolute; top: 40px; left: 0; width: 100%; text-align: center;
    font-weight: 700; font-size: 30px; letter-spacing: 1px; color: var(--ink-dark);
  }
  .letter { position: absolute; left: 84px; width: 711px; font-size: 14px; }
  .issue-date { top: 208px; }
  .recipient { top: 242px; line-height: 17px; }
  .salutation { top: 306px; }
  .body { top: 352px; line-height: 25.3px; text-align: justify; }
  .body p + p { margin-top: 25px; }
  .closing { top: 843px; }
  .signature { position: absolute; left: 84px; top: 874px; width: 200px; height: 26px; background: var(--signature); border-radius: 3px; }
  .signer-name { top: 910px; font-size: 17px; font-weight: 600; color: var(--ink-dark); }
  .signer-title { top: 936px; }
  .contact-band {
    position: absolute; left: 0; top: 1060px; width: 100%; height: 73px; background: var(--band);
    font-family: "Lato", sans-serif; color: var(--band-text);
  }
  .contact { position: absolute; top: 14px; text-align: center; font-size: 16px; line-height: 20px; }
  .contact.attorney { left: 0; width: 294px; }
  .attorney-name { color: var(--accent-bright); font-weight: 700; font-size: 19px; }
  .contact.phone { left: 294px; width: 138px; }
  .contact.web { left: 432px; width: 168px; font-size: 14px; }
  .contact.address { left: 600px; width: 281px; }
  .divider { position: absolute; top: 0; width: 1px; height: 73px; background: var(--divider); }
  .icon { position: absolute; top: 1035px; width: 34px; height: 34px; background: var(--accent); }
  .icon svg { width: 34px; height: 34px; display: block; }
</style>
</head>
<body>
<main class="letterhead">
  <div class="brand">BRY7LEGAL</div>

  <div class="letter issue-date">Issuing Date: May 5, 2018</div>
  <div class="letter recipient">Name Of Employee Mr. XYZABC<br>Address of Employee<br>Address Line 2 etc..</div>
  <div class="letter salutation">Dear Mr.XYZABC</div>
  <div class="letter body">
    <p>Lorem Ipsum has been the industry's standard dummy text ever since the 1500s, when an unknown printer took a galley of type and scrambled it to make a type specimen book. It has survived not only five centuries, but also the leap into electronic typesetting, remaining essentially unchanged. It was popularised in the 1960s with the release of Vellicor sheets containing Lorem Ipsum passages, and more recently with desktop publishing software like Quarto Layout including versions of Lorem Ipsum.</p>
    <p>Lorem Ipsum is simply dummy text of the printing and typesetting industry. Lorem Ipsum has been the industry's standard dummy text ever since the 1500s, when an unknown printer took a galley of type and scrambled it to make a type specimen book.</p>
    <p>It has survived not only five centuries, but also the leap into electronic typesetting, remaining essentially unchanged. It was popularised in the 1960s with the release of Vellicor sheets containing Lorem IpsumIpsum passages.</p>
  </div>
  <div class="letter closing">Yours Sincerely</div>
  <div class="signature" role="img" aria-label="Handwritten signature of Dorian Pell"></div>
  <div class="letter signer-name">Dorian Pell</div>
  <div class="letter signer-title">Managing Director</div>

  <div class="icon" style="left:152px">
    <svg viewBox="0 0 34 34"><circle cx="17" cy="12" r="5" fill="#fff"/><path d="M8 27c0-6 4-9 9-9s9 3 9 9z" fill="#fff"/></svg>
  </div>
  <div class="icon" style="left:347px">
    <svg viewBox="0 0 34 34"><path d="M7 14c0-4 20-4 20 0v2h-5v-2h-10v2H7z" fill="#fff"/><rect x="10" y="17" width="14" height="9" rx="2" fill="#fff"/><circle cx="17" cy="21.5" r="2.5" fill="#0677ba"/></svg>
  </div>
  <div class="icon" style="left:499px">
    <svg viewBox="0 0 34 34"><circle cx="17" cy="17" r="10" fill="#fff"/><path d="M12 12c3 0 4 3 2 5s1 5-1 7M20 9c-1 3 2 4 4 5M19 22c2-1 4 0 5-2" stroke="#0677ba" stroke-width="2" fill="none"/></svg>
  </div>
  <div class="icon" style="left:689px">
    <svg viewBox="0 0 34 34"><path d="M17 28s-8-8-8-14a8 8 0 0 1 16 0c0 6-8 14-8 14z" fill="#fff"/><circle cx="17" cy="14" r="3" fill="#0677ba"/></svg>
  </div>

  <footer class="contact-band">
    <div class="contact attorney"><div class="attorney-name">Anselmo R Quintara III</div>Attorney at Law</div>
    <div class="divider" style="left:294px"></div>
    <div class="contact phone">877-482-6017<br>469-738-1452</div>
    <div class="divider" style="left:432px"></div>
    <div class="contact web">bry@bry7legal.example<br>www.bry7legal.example</div>
    <div class="divider" style="left:600px"></div>
    <div class="contact address">2847 Larkspur Blvd<br>Ste 300, Dallas, TX 75204</div>
  </footer>
</main>
</body>
</html>
```